Business Card Design needed for start up company Halvora

In need of a new business card designed for a start up company based in Sydney, Halvora is a new start up innovative Company, our mission it to make property accessible for everyday Australian and to become the leading Real Estate platform in Australia. We want it to be fresh and clean.

Industry/Entity Type

Financial

Contact Information for Business Card

Section for Name
Section for Title

HALVORA - The Strength of Pooling
Mobile:
Direct:

Font styles to use
Sans Serif

Colors
33a6d7
0692cd
0255a3
ffffff

Requirements
Must have
• Logo, all business card details

```html
<!DOCTYPE html>
<html lang="en">
<head>
<meta charset="utf-8">
<title>Halvora Business Card</title>
<link rel="stylesheet" href="https://fonts.googleapis.com/css2?family=Open+Sans:wght@400;600;700&family=Oswald:wght@500&display=swap">
<style>
  :root {
    --backdrop: #1b1b1c;
    --card: #2a2a2b;
    --card-edge: #333334;
    --mark-circle: #1f1f20;
    --wordmark: #c4c4c4;
    --ink: #f2f2f2;
    --ink-soft: #cfcfcf;
    --accent: #33a6d7;
  }
  * { margin: 0; padding: 0; box-sizing: border-box; }
  html, body {
    width: 1200px; height: 1000px; overflow: hidden;
    background: var(--backdrop);
  }
  .canvas {
    position: relative; width: 1200px; height: 1000px;
  }
  .card {
    position: absolute; left: 280px; width: 640px; height: 365px;
    background: var(--card);
    border: 1px solid var(--card-edge);
    box-shadow: 0 18px 40px rgba(0,0,0,.45);
  }
  .card--front { top: 95px; }
  .card--back { top: 540px; }

  .logo {
    position: absolute; left: 50%; top: 50%;
    transform: translate(-50%, -50%);
    display: flex; align-items: center; gap: 14px;
  }
  .logo__circle {
    width: 74px; height: 74px; border-radius: 50%;
    background: var(--mark-circle);
  }
  .logo__name {
    font-family: "Open Sans", sans-serif; font-weight: 700;
    font-size: 58px; letter-spacing: 1px; color: var(--wordmark);
    line-height: 1;
  }

  .identity {
    position: absolute; right: 405px; top: 128px; text-align: right;
  }
  .identity__name {
    font-family: "Oswald", sans-serif; font-weight: 500;
    font-size: 34px; letter-spacing: 1.5px; color: var(--ink);
    line-height: 1.1; text-transform: uppercase;
  }
  .identity__title {
    font-family: "Open Sans", sans-serif; font-weight: 600;
    font-size: 19px; letter-spacing: 1px; color: var(--accent);
    line-height: 1.2;
  }
  .divider {
    position: absolute; left: 252px; top: 118px;
    width: 2px; height: 90px; background: var(--ink-soft);
  }
  .contacts {
    position: absolute; left: 274px; top: 116px; list-style: none;
  }
  .contacts li {
    display: flex; align-items: center; gap: 12px;
    height: 23px;
    font-family: "Open Sans", sans-serif; font-size: 16px;
    letter-spacing: .5px; color: var(--ink-soft);
  }
  .contacts svg, .address svg { width: 13px; height: 13px; fill: var(--accent); flex: none; }
  .accent { color: var(--accent); }
  .address {
    position: absolute; left: 58px; top: 280px;
    display: flex; align-items: center; gap: 12px;
    font-family: "Open Sans", sans-serif; font-size: 17px;
    letter-spacing: .6px; color: var(--ink-soft);
  }
  .address svg { width: 14px; height: 18px; }
</style>
</head>
<body>
<main class="canvas">
  <section class="card card--front" aria-label="Card front">
    <div class="logo">
      <span class="logo__circle"></span>
      <span class="logo__name">HALVORA</span>
    </div>
  </section>

  <section class="card card--back" aria-label="Card back">
    <div class="identity">
      <h1 class="identity__name">Darien Kell</h1>
      <p class="identity__title">Director</p>
    </div>
    <span class="divider"></span>
    <ul class="contacts">
      <li>
        <svg viewBox="0 0 24 24"><path d="M6.6 10.8a15.1 15.1 0 0 0 6.6 6.6l2.2-2.2c.3-.3.7-.4 1-.2 1.1.4 2.3.6 3.6.6.6 0 1 .4 1 1V20c0 .6-.4 1-1 1A17 17 0 0 1 3 4c0-.6.4-1 1-1h3.5c.6 0 1 .4 1 1 0 1.3.2 2.5.6 3.6.1.3 0 .7-.2 1z"/></svg>
        000 123 456 789
      </li>
      <li>
        <svg viewBox="0 0 24 24"><path d="M7 1h10a2 2 0 0 1 2 2v18a2 2 0 0 1-2 2H7a2 2 0 0 1-2-2V3a2 2 0 0 1 2-2zm0 3v14h10V4zm5 15.5a1.2 1.2 0 1 0 0 2.4 1.2 1.2 0 0 0 0-2.4z"/></svg>
        000 222 3334
      </li>
      <li>
        <svg viewBox="0 0 24 24"><path d="M2 5h20v14H2zm2 2v.5l8 5.5 8-5.5V7zm0 2.9V17h16V9.9l-8 5.5z"/></svg>
        urname@email.com
      </li>
      <li>
        <svg viewBox="0 0 24 24"><path d="M12 2a10 10 0 1 0 0 20 10 10 0 0 0 0-20zm6.9 6h-3a15.6 15.6 0 0 0-1.3-3.9A8 8 0 0 1 18.9 8zM12 4c.8 1.2 1.5 2.5 1.9 4h-3.8c.4-1.5 1.1-2.8 1.9-4zM4.3 14a8 8 0 0 1 0-4h3.4a16 16 0 0 0 0 4zm.8 2h3a15.6 15.6 0 0 0 1.3 3.9A8 8 0 0 1 5.1 16zm3-8h-3a8 8 0 0 1 4.3-3.9C8.8 5.3 8.4 6.6 8.1 8zM12 20c-.8-1.2-1.5-2.5-1.9-4h3.8c-.4 1.5-1.1 2.8-1.9 4zm2.3-6H9.7a14.6 14.6 0 0 1 0-4h4.6a14.6 14.6 0 0 1 0 4zm.3 5.9c.6-1.2 1-2.5 1.3-3.9h3a8 8 0 0 1-4.3 3.9zm1.7-5.9a16 16 0 0 0 0-4h3.4a8 8 0 0 1 0 4z"/></svg>
        <span>www.<span class="accent">websitename</span>.com</span>
      </li>
    </ul>
    <p class="address">
      <svg viewBox="0 0 16 22"><path d="M8 0a8 8 0 0 0-8 8c0 6 8 14 8 14s8-8 8-14a8 8 0 0 0-8-8zm0 11a3 3 0 1 1 0-6 3 3 0 0 1 0 6z"/></svg>
      Your Street Address, Sydney, 1234
    </p>
  </section>
</main>
</body>
</html>
```